K.R Landscaping 484-883-7758Mulching Mowing Planting Spring and Fall Clean up

The colors I would like to work with Are black and green.I do have a Facebook page it's https://www.examplesocial.net/KR-Landscaping-518203946172834/

For my business logo I would like to put that either on the corner or in the background

Services: mowing, mulching, fall and spring cleanup, hedge trimming

Industry/Entity Type

Landscaping

Requirements
Must have
• Please use these pics
• I like Design #9926064
• and room for addresses to
Should not have
• the pics in the back of card

```html
<!DOCTYPE html>
<html lang="en">
<head>
<meta charset="utf-8">
<title>K.R Landscaping Postcard</title>
<link rel="stylesheet" href="https://fonts.googleapis.com/css2?family=Roboto+Condensed:wght@400;700&family=Great+Vibes&family=Open+Sans:wght@400;600&display=swap">
<style>
  :root {
    --green: #55b92f;
    --green-dark: #3d8f1f;
    --black: #141414;
    --charcoal: #262626;
    --white: #ffffff;
    --paper: #f4f4f4;
    --stage: #e2e2e2;
    --text-grey: #3a3a3a;
  }
  * { box-sizing: border-box; margin: 0; padding: 0; }
  html, body { width: 900px; height: 1200px; overflow: hidden; }
  body {
    background: var(--stage);
    font-family: "Roboto Condensed", "Arial Narrow", sans-serif;
    position: relative;
  }
  .card {
    position: absolute;
    left: 40px;
    width: 820px;
    height: 540px;
    overflow: hidden;
    box-shadow: 0 6px 18px rgba(0,0,0,.25);
  }
  .card--front { top: 40px; background: var(--black); }
  .card--back { top: 620px; background: var(--white); }

  /* FRONT */
  .hero-photo {
    position: absolute; inset: 0 0 140px 0;
    background: linear-gradient(160deg, #6f9fd0 0%, #a8c7e3 22%, #6d8f4a 45%, #3f6b26 70%, #5b8a3a 100%);
  }
  .front-shape { position: absolute; inset: 0; }
  .brand {
    position: absolute; left: 28px; top: 26px; width: 260px;
    color: var(--white);
  }
  .brand__name {
    display: block;
    font-family: "Roboto Condensed", sans-serif;
    font-weight: 700; font-size: 40px; line-height: 1; letter-spacing: 1px;
  }
  .brand__tagline {
    display: block; margin-top: 8px;
    font-family: "Great Vibes", cursive;
    font-size: 19px; line-height: 1.1;
  }
  .services-title {
    position: absolute; left: 0; top: 218px;
    width: 200px; height: 40px;
    background: var(--green);
    border-radius: 0 20px 20px 0;
    color: var(--white); font-weight: 700; font-size: 27px;
    padding-left: 18px; line-height: 40px;
    white-space: nowrap;
  }
  .services-list { position: absolute; left: 10px; top: 272px; list-style: none; }
  .service {
    display: flex; align-items: center; gap: 10px;
    width: 222px; height: 30px; margin-bottom: 10px;
    background: var(--green);
    color: var(--white); font-size: 17px; font-weight: 700; line-height: 1;
    padding-left: 4px;
    white-space: nowrap;
  }
  .service__tick {
    width: 22px; height: 22px; flex: none;
    border: 2px solid var(--white);
    display: flex; align-items: center; justify-content: center;
  }
  .project-photo {
    position: absolute; width: 128px; height: 128px; border-radius: 50%;
    border: 6px solid var(--white);
  }
  .project-photo--fence { left: 440px; top: 268px; background: radial-gradient(circle at 50% 40%, #8fb86a, #4f7f2d 70%); }
  .project-photo--yard  { left: 582px; top: 268px; background: radial-gradient(circle at 50% 45%, #b9a98a, #6a7c4a 70%); }
  .call-now {
    position: absolute; right: 40px; top: 458px;
    display: flex; align-items: center; gap: 10px;
    color: var(--white); font-size: 32px; font-weight: 400;
    white-space: nowrap;
  }
  .call-now__icon {
    width: 30px; height: 30px; border-radius: 50%;
    background: var(--green);
    display: flex; align-items: center; justify-content: center;
  }

  /* BACK */
  .back-shape { position: absolute; inset: 0; }
  .intro-text {
    position: absolute; left: 40px; top: 36px; width: 218px;
    font-family: "Open Sans", sans-serif;
    font-size: 15px; line-height: 1.32; color: var(--text-grey);
  }
  .back-brand {
    position: absolute; left: 420px; top: 40px; width: 170px; text-align: center;
    color: var(--black);
  }
  .back-brand__name { font-weight: 700; font-size: 22px; letter-spacing: 1px; line-height: 1.15; }
  .back-brand__tagline { font-family: "Great Vibes", cursive; font-size: 12px; margin-top: 2px; }
  .stamp {
    position: absolute; right: 30px; top: 26px;
    width: 70px; height: 84px; border: 2px solid #777;
  }
  .contact {
    position: absolute; left: 30px; top: 358px; width: 500px;
    color: var(--white); font-family: "Open Sans", sans-serif;
  }
  .contact__title { font-family: "Roboto Condensed", sans-serif; font-size: 22px; font-weight: 700; margin-bottom: 8px; }
  .contact__grid { display: grid; grid-template-columns: 190px 1fr; row-gap: 8px; font-size: 15px; }
  .contact__item { display: flex; align-items: center; gap: 8px; white-space: nowrap; }
  .dot { width: 16px; height: 16px; border-radius: 50%; background: var(--white); flex: none; }
</style>
</head>
<body>

<section class="card card--front" aria-label="Postcard front">
  <div class="hero-photo" role="img" aria-label="Photo of a landscaped backyard with lawn, trees and a house"></div>

  <svg class="front-shape" viewBox="0 0 820 540" aria-hidden="true">
    <path d="M0 205 C220 215 380 330 820 360 L820 540 L0 540 Z" fill="var(--black)"/>
    <path d="M0 205 C220 215 380 330 820 360" fill="none" stroke="var(--green)" stroke-width="8"/>
    <path d="M0 160 C220 170 330 215 460 250" fill="none" stroke="var(--green)" stroke-width="4" opacity=".8"/>
  </svg>

  <div class="brand">
    <span class="brand__name">K.R LANDSCAPING</span>
    <span class="brand__tagline">For all your Professional Landscaping Needs</span>
  </div>

  <div class="services-title">Our Services</div>
  <ul class="services-list">
    <li class="service"><span class="service__tick"><svg width="14" height="12" viewBox="0 0 14 12"><path d="M1 6l4 4 8-9" fill="none" stroke="#fff" stroke-width="2.5"/></svg></span>Mulching Mowing</li>
    <li class="service"><span class="service__tick"><svg width="14" height="12" viewBox="0 0 14 12"><path d="M1 6l4 4 8-9" fill="none" stroke="#fff" stroke-width="2.5"/></svg></span>Planting Plants</li>
    <li class="service"><span class="service__tick"><svg width="14" height="12" viewBox="0 0 14 12"><path d="M1 6l4 4 8-9" fill="none" stroke="#fff" stroke-width="2.5"/></svg></span>Fall &amp; Spring Clean up</li>
    <li class="service"><span class="service__tick"><svg width="14" height="12" viewBox="0 0 14 12"><path d="M1 6l4 4 8-9" fill="none" stroke="#fff" stroke-width="2.5"/></svg></span>Hedge Trimming</li>
  </ul>

  <div class="project-photo project-photo--fence" role="img" aria-label="Photo of a garden fence and lawn"></div>
  <div class="project-photo project-photo--yard" role="img" aria-label="Photo of a finished patio and planting bed"></div>

  <div class="call-now">
    <span>Call Now:</span>
    <span class="call-now__icon"><svg width="16" height="16" viewBox="0 0 24 24"><path d="M6.6 10.8a15 15 0 006.6 6.6l2.2-2.2a1 1 0 011-.25 11.4 11.4 0 003.6.57 1 1 0 011 1V20a1 1 0 01-1 1A17 17 0 013 4a1 1 0 011-1h3.5a1 1 0 011 1 11.4 11.4 0 00.57 3.6 1 1 0 01-.25 1z" fill="#fff"/></svg></span>
    <span>392-615-0248</span>
  </div>
</section>

<section class="card card--back" aria-label="Postcard back">
  <svg class="back-shape" viewBox="0 0 820 540" aria-hidden="true">
    <path d="M0 0 L270 0 C300 90 300 220 260 320 L0 320 Z" fill="var(--paper)"/>
    <path d="M270 0 C300 90 300 220 260 320" fill="none" stroke="var(--green)" stroke-width="10"/>
    <path d="M285 0 C318 90 318 230 276 330" fill="none" stroke="var(--black)" stroke-width="5"/>
    <path d="M0 330 L560 330 C600 380 600 440 560 500 L0 500 Z" fill="var(--green)"/>
    <path d="M0 330 L560 330 C590 350 600 372 604 396" fill="none" stroke="var(--black)" stroke-width="6"/>
    <rect x="0" y="500" width="820" height="12" fill="var(--charcoal)"/>
  </svg>

  <p class="intro-text">Lorem Ipsum is simply dummy text of the printing and typesetting industry. Lorem Ipsum has been the industry's standard dummy text ever since the 1500s, when an unknown printer took a galley of type and scrambled it to make a type specimen book.</p>

  <div class="back-brand">
    <div class="back-brand__name">K.R<br>LANDSCAPING</div>
    <div class="back-brand__tagline">For all your landscaping needs</div>
  </div>

  <div class="stamp" aria-label="Stamp area"></div>

  <div class="contact">
    <div class="contact__title">Contact info</div>
    <div class="contact__grid">
      <div class="contact__item"><svg width="14" height="18" viewBox="0 0 14 18"><path d="M7 0a7 7 0 00-7 7c0 5 7 11 7 11s7-6 7-11a7 7 0 00-7-7zm0 10a3 3 0 110-6 3 3 0 010 6z" fill="#fff"/></svg>Address line 1</div>
      <div class="contact__item">Follow Us <span class="dot"></span></div>
      <div class="contact__item"><svg width="14" height="18" viewBox="0 0 14 18"><path d="M7 0a7 7 0 00-7 7c0 5 7 11 7 11s7-6 7-11a7 7 0 00-7-7zm0 10a3 3 0 110-6 3 3 0 010 6z" fill="#fff"/></svg>Address line 2</div>
      <div class="contact__item"><svg width="16" height="16" viewBox="0 0 24 24"><path d="M6.6 10.8a15 15 0 006.6 6.6l2.2-2.2a1 1 0 011-.25 11.4 11.4 0 003.6.57 1 1 0 011 1V20a1 1 0 01-1 1A17 17 0 013 4a1 1 0 011-1h3.5a1 1 0 011 1 11.4 11.4 0 00.57 3.6 1 1 0 01-.25 1z" fill="#fff"/></svg>392-615-0248</div>
      <div class="contact__item"><svg width="18" height="13" viewBox="0 0 18 13"><rect x="1" y="1" width="16" height="11" fill="none" stroke="#fff" stroke-width="1.6"/><path d="M1 1l8 6 8-6" fill="none" stroke="#fff" stroke-width="1.6"/></svg>krservice@example.com</div>
    </div>
  </div>
</section>

</body>
</html>
```